professional business card design

Business card design. Photos have been uploaded and i am open to the designer choosing which photos to use. Would like the card to be mostyly in a grey scale design with black, whites, silver & grey colours. I have added copy of our flyer as would like on the back side of card our services to be listed. Do not use any bright colurs such as blue red green or yellow. i need to be able to edit the phone number and naem in the final card design submitted.

Target Market(s)

Clients

Industry/Entity Type

earhmovibng and transport

Contact Information for Business Card

Director Name, address, email, phone number and services

Colors

Designer to choose only greyscale colors for use in the design.

Requirements
Should not have
• no yellow, red, blue or green

```html
<!DOCTYPE html>
<html lang="en">
<head>
<meta charset="utf-8">
<title>Kestrel Haul – Business Card</title>
<link href="https://fonts.googleapis.com/css2?family=Poppins:ital,wght@0,400;0,600;0,700;1,400&display=swap" rel="stylesheet">
<style>
  :root {
    --stage: #2b2b2b;
    --card-black: #050505;
    --mesh-dark: #0d0d0d;
    --mesh-light: #2a2a2a;
    --silver-light: #f2f2f2;
    --silver-mid: #bdbdbd;
    --silver-dark: #7d7d7d;
    --white: #ffffff;
    --ink: #0a0a0a;
  }
  * { box-sizing: border-box; margin: 0; padding: 0; }
  html, body { width: 1200px; height: 866px; overflow: hidden; }
  body {
    background: var(--stage);
    font-family: "Poppins", sans-serif;
    display: flex;
    align-items: center;
    justify-content: center;
    gap: 40px;
  }
  .card {
    position: relative;
    width: 540px;
    height: 309px;
    overflow: hidden;
    background: var(--card-black);
    box-shadow: 0 14px 30px rgba(0,0,0,.55);
    color: var(--white);
  }
  /* ---------- front ---------- */
  .card-front .mesh {
    position: absolute; inset: 0;
    background: radial-gradient(ellipse at 62% 45%, var(--mesh-light) 0%, var(--mesh-dark) 55%, var(--card-black) 100%);
  }
  .brand {
    position: absolute;
    left: 300px; top: 70px;
    width: 220px;
    display: flex; align-items: center; gap: 10px;
    font-weight: 700;
    font-size: 30px;
    line-height: 1;
    color: var(--silver-mid);
    letter-spacing: 1px;
    text-transform: uppercase;
  }
  .brand-mark {
    width: 18px; height: 18px; flex: none;
    background: var(--silver-mid);
  }
  .holder { position: absolute; left: 28px; top: 36px; }
  .holder-name {
    font-weight: 700; font-size: 21px; letter-spacing: 1px;
    text-transform: uppercase; line-height: 1.1;
  }
  .holder-role { font-size: 14px; color: var(--silver-light); margin-top: 2px; }
  .holder-rule { width: 250px; height: 1px; background: var(--silver-mid); margin: 8px 0 8px; }
  .contact-line {
    display: flex; align-items: center; gap: 8px;
    font-size: 14px; line-height: 1.55;
  }
  .contact-line svg { width: 13px; height: 13px; flex: none; }
  .address {
    position: absolute; right: 26px; top: 184px;
    text-align: left; font-size: 15px; line-height: 1.3; width: 240px;
  }
  .address-rule {
    position: absolute; right: 26px; top: 228px;
    width: 260px; height: 1px; background: var(--silver-mid);
  }
  .front-band { position: absolute; left: 0; bottom: 0; width: 540px; height: 64px; }
  .website {
    position: absolute; right: 40px; bottom: 16px;
    font-size: 15px; color: var(--ink); letter-spacing: .5px;
  }
  /* ---------- back ---------- */
  .photo {
    position: absolute; left: 0; top: 0; width: 540px; height: 118px;
    background: linear-gradient(180deg, #0b0b0b 0%, #2c2722 60%, #5a4a3a 100%);
  }
  .back-brand {
    position: absolute; right: 26px; top: 26px;
    display: flex; align-items: center; gap: 8px;
    font-weight: 700; font-size: 22px; color: var(--silver-mid);
    text-transform: uppercase; letter-spacing: 1px;
  }
  .back-brand .brand-mark { width: 14px; height: 14px; }
  .services-band {
    position: absolute; left: 0; top: 118px; width: 540px; height: 26px;
    background: linear-gradient(90deg, var(--silver-dark), var(--silver-light) 40%, var(--silver-mid) 70%, var(--silver-light));
  }
  .services-title {
    position: absolute; right: 150px; top: 2px;
    font-weight: 700; font-size: 16px; color: var(--ink); letter-spacing: 1px;
  }
  .services {
    position: absolute; left: 0; top: 152px; width: 540px;
    text-align: center; font-size: 12.5px; line-height: 1.45;
  }
  .services-note {
    position: absolute; left: 0; top: 238px; width: 540px;
    text-align: center; font-size: 10.5px; font-style: italic;
  }
  .cta-band {
    position: absolute; left: 0; bottom: 0; width: 540px; height: 40px;
    background: linear-gradient(90deg, var(--silver-light), var(--silver-mid) 35%, var(--silver-light) 65%, var(--silver-dark));
    display: flex; align-items: center; justify-content: center;
    font-weight: 700; font-size: 14px; color: var(--ink);
  }
</style>
</head>
<body>

  <section class="card card-front" aria-label="Business card front">
    <div class="mesh" role="img" aria-label="Dark metal mesh texture"></div>

    <div class="brand"><span class="brand-mark"></span>Kestrel Haul</div>

    <div class="holder">
      <div class="holder-name">Marcus Hale</div>
      <div class="holder-role">Managing Director</div>
      <div class="holder-rule"></div>
      <div class="contact-line">
        <svg viewBox="0 0 16 16" aria-hidden="true"><path fill="#fff" d="M3.6 1.2l2.3 2.6-1.2 1.8c.9 2 2.6 3.7 4.6 4.6l1.8-1.2 2.6 2.3-1.2 2.6C7 13.5 2.5 9 1 3.6z"/></svg>
        <span>055-310 872 416</span>
      </div>
      <div class="contact-line">
        <svg viewBox="0 0 16 16" aria-hidden="true"><rect x="1" y="3" width="14" height="10" fill="#fff"/><path d="M1 3l7 6 7-6" fill="none" stroke="#000" stroke-width="1.2"/></svg>
        <span>office@kestrelhaul.com</span>
      </div>
    </div>

    <div class="address">87 Quarry Ridge Road<br>60318, Stonebrook</div>
    <div class="address-rule"></div>

    <svg class="front-band" viewBox="0 0 540 64" preserveAspectRatio="none" aria-hidden="true">
      <defs>
        <linearGradient id="brushed" x1="0" x2="1" y1="0" y2="0">
          <stop offset="0" stop-color="#8a8a8a"/>
          <stop offset=".35" stop-color="#f4f4f4"/>
          <stop offset=".6" stop-color="#b5b5b5"/>
          <stop offset=".85" stop-color="#efefef"/>
          <stop offset="1" stop-color="#9a9a9a"/>
        </linearGradient>
      </defs>
      <path d="M0 26 L200 26 C222 26 226 14 248 14 L540 14 L540 64 L0 64 Z" fill="url(#brushed)"/>
      <path d="M0 20 L196 20 C218 20 222 8 244 8 L540 8" fill="none" stroke="#9c9c9c" stroke-width="2"/>
      <rect x="0" y="26" width="190" height="38" fill="#050505"/>
    </svg>
    <div class="website">www.kestrelhaul.com</div>
  </section>

  <section class="card card-back" aria-label="Business card back">
    <div class="photo" role="img" aria-label="Photo of a road train tipper truck at dusk"></div>
    <div class="back-brand"><span class="brand-mark"></span>Kestrel Haul</div>

    <div class="services-band"><span class="services-title">OUR SERVICES</span></div>

    <p class="services">
      Over size loads/hot shot loads | Heavy vehicle recovery services<br>
      Potable water deliveries | Road building/maintenance | Equipment &amp; operators<br>
      Sand &amp; metal supply &amp; cartage | Road train tippers | Road train tankers<br>
      Earthworks | Road train flat tops | Drop deck trailers | Mine site accredited
    </p>
    <p class="services-note">we offer a large range of services not listed.</p>

    <div class="cta-band">So call us today for a personalised quote to suit your needs.</div>
  </section>

</body>
</html>
```